Communication and Marketing agency needs a new presentation card

We are a group of communication and marketing agencies specialized in companies that are in the logistics and industrial sector. The head agency is TELVANO Grupo and the group consists of 4 agencies: TELVANO Media, TELVANO Digital, TELVANO Research and DifundeEnPantalla. We hace 4 offices in Spain (Madrid, Barcelona, Valencia and Murcia). We are looking for a clean and attractive design that transmits our experience, brand presence in the market and knowledge to those who receive the card.It has to maintain the colors of the logo that is attached.
Target Market(s)
logistics and industrial sector
Marketing department
Contact Information for Business Card
Clean and attractive design

```html
<!DOCTYPE html>
<html lang="es">
<head>
<meta charset="utf-8">
<title>TELVANO Grupo — Tarjeta de presentación</title>
<link rel="stylesheet" href="https://fonts.googleapis.com/css2?family=Montserrat:wght@300;400;600;700&display=swap">
<style>
  :root {
    --backdrop: #e9e7e4;
    --card-dark: #2f2c2d;
    --card-dark-deep: #242223;
    --band-white: #f4f4f4;
    --band-grey: #4a4748;
    --city-grey: #6c696a;
    --brand-red: #c8232e;
    --text-grey: #555253;
    --title-grey: #6a6768;
  }
  * { box-sizing: border-box; margin: 0; padding: 0; }
  html, body {
    width: 1200px; height: 900px; overflow: hidden;
    background: var(--backdrop);
    font-family: "Montserrat", Arial, sans-serif;
  }
  .sheet {
    width: 1200px; height: 900px;
    display: flex; flex-direction: column;
    align-items: center; justify-content: center; gap: 44px;
  }
  .card {
    position: relative;
    width: 580px; height: 376px;
    background: linear-gradient(180deg, var(--card-dark) 0%, var(--card-dark-deep) 100%);
    box-shadow: 0 10px 26px rgba(0,0,0,.25);
    overflow: hidden;
  }

  /* Front */
  .front .group-name {
    position: absolute; left: 0; right: 0; top: 74px;
    text-align: center;
    font-size: 52px; font-weight: 700; letter-spacing: 1px;
    color: var(--brand-red); line-height: 1;
    white-space: nowrap;
  }
  .front .agency-band {
    position: absolute; left: 0; right: 0; top: 184px; height: 64px;
    background: var(--band-white);
    display: grid; grid-template-columns: repeat(4, 1fr);
    align-items: center; justify-items: center;
    column-gap: 10px;
    padding: 0 20px;
  }
  .agency {
    font-size: 12px; font-weight: 600; color: var(--text-grey);
    white-space: nowrap;
  }
  .agency.accent { color: var(--brand-red); }
  .front .city-band {
    position: absolute; left: 0; right: 0; top: 248px; height: 46px;
    background: var(--band-grey);
    display: flex; align-items: center; justify-content: center;
  }
  .cities {
    font-size: 17px; font-weight: 700; letter-spacing: 2px;
    color: var(--city-grey); text-transform: uppercase;
    white-space: nowrap;
  }

  /* Back */
  .back .name-band {
    position: absolute; left: 0; right: 0; top: 196px; height: 118px;
    background: var(--band-white);
    padding: 22px 52px;
  }
  .person-name {
    font-size: 30px; font-weight: 300; color: var(--brand-red); line-height: 1.2;
  }
  .person-title {
    font-size: 30px; font-weight: 300; color: var(--title-grey); line-height: 1.2;
  }
</style>
</head>
<body>
  <main class="sheet">
    <section class="card front" aria-label="Anverso de la tarjeta">
      <h1 class="group-name">TELVANO Grupo</h1>
      <div class="agency-band">
        <span class="agency">TELVANO Digital</span>
        <span class="agency">TELVANO Media</span>
        <span class="agency">TELVANO Research</span>
        <span class="agency accent">DifundeEnPantalla</span>
      </div>
      <div class="city-band">
        <p class="cities">Madrid · Barcelona · Valencia · Murcia</p>
      </div>
    </section>

    <section class="card back" aria-label="Reverso de la tarjeta">
      <div class="name-band">
        <p class="person-name">Lucía Ortega</p>
        <p class="person-title">Director</p>
      </div>
    </section>
  </main>
</body>
</html>
```